Dietitian needs awesome business card

I need a contemporary design that's eye catching but professional.
My card is to given to doctors, specialists and patients alike.
I manage patients with chronic diseases
I have uploaded my logo and current business card, I would also like the other Certified Clinical Nutritionist logo incorporated into the design

Target Market(s)

Doctors, specialists and patients

Industry/Entity Type

Healthcare

Contact Information for Business Card

www.brightfieldnutrition.com.au
Ph: 0427 561 903
Fax: 6457 2183
email: marcus.k.diet@fernmail.com
Space on the back of the card with: Appointment date, Appointment time and appointment location

Font styles to use
Serif

Colors
fbee3e
876aae
ffc214

Requirements
Must have
• My Logo
• Certified Clinical Nutritionist Logo
• My 4 locations - Pinebrook Medical Centre, North Corrin Health, Hollis Medical, Ashcombe Doctors Surgery
Nice to have
• I like the colours in my current business card

```html
<!DOCTYPE html>
<html lang="en">
<head>
<meta charset="utf-8">
<title>Brightfield Nutrition &amp; Dietetics – Business Card</title>
<link rel="stylesheet" href="https://fonts.googleapis.com/css2?family=Signika:wght@300;400&family=Noto+Serif:wght@400&display=swap">
<style>
  :root {
    --page-bg: #d9dadb;
    --card-bg: #ffffff;
    --brand-blue: #1f3b93;
    --navy: #17246e;
    --mid-blue: #1f5fb8;
    --brand-green: #8cc63f;
    --text-grey: #4a4a4a;
    --badge-orange: #f47b20;
    --forest-dark: #3b4a33;
    --forest-mid: #56664a;
  }
  * { box-sizing: border-box; margin: 0; padding: 0; }
  html, body {
    width: 1105px; height: 1200px; overflow: hidden;
    background: var(--page-bg);
    font-family: "Signika", Arial, sans-serif;
  }
  .card {
    position: absolute; left: 182px;
    width: 747px; height: 425px;
    background: var(--card-bg);
    overflow: hidden;
  }
  .card--front { top: 119px; }
  .card--back { top: 637px; }

  /* Front */
  .brand { position: absolute; left: 55px; top: 66px; display: flex; align-items: center; gap: 14px; }
  .brand__dot { width: 100px; height: 100px; border-radius: 50%; background: var(--brand-blue); }
  .brand__name { color: var(--brand-blue); font-weight: 400; font-size: 30px; line-height: 1.15; }
  .person { position: absolute; left: 48px; top: 228px; }
  .person__name { color: var(--brand-blue); font-size: 29px; font-weight: 400; }
  .person__role { color: var(--brand-green); font-size: 20px; font-weight: 300; margin-top: 4px; }
  .contacts { position: absolute; left: 48px; top: 308px; display: flex; gap: 14px; color: var(--text-grey); font-size: 20px; font-weight: 300; }
  .contact { display: flex; align-items: center; gap: 6px; }
  .contact svg { width: 18px; height: 18px; fill: var(--brand-blue); }
  .web-band {
    position: absolute; left: 0; top: 366px; width: 100%; height: 40px;
    background: linear-gradient(90deg, var(--navy) 0%, var(--mid-blue) 60%, #1b7fc4 78%, var(--brand-green) 92%, #a9d63f 100%);
  }
  .web-band__url { position: absolute; left: 46px; top: 8px; color: #fff; font-family: "Noto Serif", Georgia, serif; font-size: 19px; letter-spacing: 1.4px; }
  .web-band__dot { position: absolute; left: 600px; top: -14px; width: 56px; height: 56px; border-radius: 50%; background: #fff; border: 3px solid var(--brand-green); }

  /* Back */
  .back-glow {
    position: absolute; left: -10px; top: 40px; width: 350px; height: 350px; border-radius: 50%;
    background: radial-gradient(circle at 40% 40%, rgba(31,95,184,0.10), rgba(140,198,63,0.12));
  }
  .appointment { position: absolute; left: 56px; top: 212px; color: var(--brand-blue); font-size: 21px; font-weight: 300; }
  .appointment__row { display: flex; align-items: baseline; gap: 6px; height: 40px; }
  .appointment__line { border-bottom: 2px dotted var(--brand-blue); height: 14px; }
  .appointment__line--date { width: 210px; }
  .appointment__line--time { width: 148px; }
  .appointment__line--location { width: 180px; }
  .appointment__ampm { font-size: 15px; }
  .clinics { position: absolute; left: 511px; top: 96px; width: 200px; color: var(--brand-blue); font-size: 16px; font-weight: 300; line-height: 1.5; list-style: none; }
  .clinics__item::before { content: ""; display: inline-block; width: 6px; height: 6px; border-radius: 50%; background: var(--brand-green); margin: 0 8px 2px 0; }
  .cert-badge { position: absolute; left: 511px; top: 243px; width: 179px; height: 83px; background: var(--badge-orange); border-radius: 3px; }
  .cert-badge__circle { position: absolute; right: 12px; top: 12px; width: 59px; height: 59px; border-radius: 50%; background: #fff; }
  .region-band {
    position: absolute; left: 0; top: 370px; width: 100%; height: 55px;
    background: linear-gradient(90deg, var(--forest-dark), var(--forest-mid) 50%, var(--forest-dark));
    display: flex; align-items: center; justify-content: center;
  }
  .region-band__text { color: #fff; font-family: "Noto Serif", Georgia, serif; font-size: 24px; }
</style>
</head>
<body>
  <section class="card card--front">
    <div class="brand">
      <div class="brand__dot"></div>
      <div class="brand__name">Brightfield<br>Nutrition &amp; Dietetics</div>
    </div>
    <div class="person">
      <div class="person__name">Marcus Kellaway</div>
      <div class="person__role">Nutritionist &amp; Chef</div>
    </div>
    <div class="contacts">
      <span class="contact">
        <svg viewBox="0 0 24 24" aria-hidden="true"><path d="M6.6 10.8a15 15 0 0 0 6.6 6.6l2.2-2.2a1 1 0 0 1 1-.25 11.4 11.4 0 0 0 3.6.57 1 1 0 0 1 1 1V20a1 1 0 0 1-1 1A17 17 0 0 1 3 4a1 1 0 0 1 1-1h3.5a1 1 0 0 1 1 1c0 1.25.2 2.45.57 3.57a1 1 0 0 1-.25 1z"/></svg>
        0427 561 903
      </span>
      <span class="contact">
        <svg viewBox="0 0 24 24" aria-hidden="true"><path d="M6 2h12v6H6zM3 9h18a1 1 0 0 1 1 1v8h-4v4H6v-4H2v-8a1 1 0 0 1 1-1zm5 7v4h8v-4z"/></svg>
        6457 2183
      </span>
      <span class="contact">
        <svg viewBox="0 0 24 24" aria-hidden="true"><path d="M2 5h20v14H2zm2 2v.5l8 5 8-5V7l-8 5z"/></svg>
        marcus.k.diet@fernmail.com
      </span>
    </div>
    <div class="web-band">
      <span class="web-band__url">www.brightfieldnutrition.com.au</span>
      <div class="web-band__dot"></div>
    </div>
  </section>

  <section class="card card--back">
    <div class="back-glow"></div>
    <ul class="clinics">
      <li class="clinics__item">Pinebrook Medical Centre</li>
      <li class="clinics__item">North Corrin Health</li>
      <li class="clinics__item">Hollis Medical</li>
      <li class="clinics__item">Ashcombe Doctors Surgery</li>
    </ul>
    <div class="appointment">
      <div class="appointment__row">Date : <span class="appointment__line appointment__line--date"></span></div>
      <div class="appointment__row">Time : <span class="appointment__line appointment__line--time"></span><span class="appointment__ampm">AM/PM</span></div>
      <div class="appointment__row">Location : <span class="appointment__line appointment__line--location"></span></div>
    </div>
    <div class="cert-badge" role="img" aria-label="Certified Clinical Nutritionist badge">
      <div class="cert-badge__circle"></div>
    </div>
    <div class="region-band">
      <span class="region-band__text">Dietitian for Corrindale &amp; the North East Valley</span>
    </div>
  </section>
</body>
</html>
```